8'x8' Exhibit Backdrop for Healthcare Events focused on the 55 and older crowds

8X8 Backdrop for Exhibiting.

I also want a design for a 6' table skirt to include our logo on two sides and the logo with Hereditary Cancer Screening underneath on the front. I want the main message of Will You Give your Loved Ones The Information To Beat Cancer in Their Lives to be completely centered on the 8X8 backdrop. Hereditary Cancer Screening The Test You Take For Them in the top left corner and the purple box on the right hand side - just like the photo that has been uploaded below. I need High resolution photos around the backdrop but not so large that they overtake the main message.

Target Market(s)

55+ crowd living in Adult only communities. They have an active lifestyle

Industry/Entity Type

Healthcare

Other font styles liked:
• "The Test You Take For Them" is Comic Sans

Colors
0255a3
fbed22
ffffff

Requirements
Must have
• I am posting a photo of the exact backdrop I would like to see. There are red arrows showing where to move certain items. There is a space underneath the slogan WILL YOU GIVE YOUR LOVED ONES... where another photo will go. Add another photo underneath the slogan that you are moving up - GIVE THEM THE GIFT OF KNOWLEDGE
• See the upload section for the new photo
• Do this one exactly like I am asking for and then you can show me some of your ideas. Thanks
• THE PHOTOS UPLOADED ARE EXAMPLES. FEEL FREE TO SEARCH OUT YOUR OWN HIGH RESOLUTION PHOTOS. THANKS

```html
<!DOCTYPE html>
<html lang="en">
<head>
<meta charset="utf-8">
<title>Hereditary Cancer Screening Backdrop</title>
<link href="https://fonts.googleapis.com/css2?family=Montserrat:wght@400;600;700&family=Oswald:wght@300;400;500;600;700&display=swap" rel="stylesheet">
<style>
  :root {
    --navy: #0c1e5e;
    --green: #7dc242;
    --white: #ffffff;
    --page: #e4e4e4;
    --photo-warm-a: #c9a07e;
    --photo-warm-b: #7f5d46;
    --photo-soft-a: #d8c8b4;
    --photo-soft-b: #9a8a78;
    --photo-green-a: #9bb77a;
    --photo-green-b: #5e6f45;
  }
  * { margin: 0; padding: 0; box-sizing: border-box; }
  html, body { width: 1200px; height: 1200px; overflow: hidden; background: var(--page); }
  .backdrop {
    position: absolute; left: 0; top: 51px; width: 1200px; height: 1098px;
    background: var(--white); font-family: 'Montserrat', sans-serif; color: var(--navy);
  }
  .photo { position: absolute; background: linear-gradient(135deg, var(--photo-warm-a), var(--photo-warm-b)); }
  .photo.soft { background: linear-gradient(135deg, var(--photo-soft-a), var(--photo-soft-b)); }
  .photo.garden { background: linear-gradient(135deg, var(--photo-green-a), var(--photo-green-b)); }

  .title { position: absolute; right: 815px; top: 78px; text-align: right; line-height: 1; }
  .title .lead { font-weight: 700; font-size: 64px; letter-spacing: 1px; }
  .title .line { font-weight: 400; font-size: 60px; letter-spacing: 1px; margin-top: -4px; }
  .tagline {
    position: absolute; left: 37px; top: 260px; width: 349px; height: 30px;
    background: var(--green); color: var(--white); font-weight: 600; font-size: 22px;
    text-align: center; line-height: 30px;
  }

  .headline { position: absolute; left: 389px; width: 411px; font-family: 'Oswald', sans-serif; text-transform: uppercase; text-align: center; color: var(--navy); line-height: 1; white-space: nowrap; }
  .headline.ask { top: 414px; font-size: 77px; font-weight: 300; letter-spacing: -2px; }
  .headline.ask strong { font-weight: 700; }
  .headline.loved { top: 500px; font-size: 59px; font-weight: 300; letter-spacing: -1px; }
  .info-bar {
    position: absolute; left: 389px; top: 581px; width: 411px; height: 52px;
    background: var(--navy); color: var(--white); font-weight: 700; font-size: 29px;
    line-height: 52px; text-align: center; letter-spacing: 0.5px; white-space: nowrap;
  }
  .rule-v { position: absolute; left: 389px; top: 633px; width: 11px; height: 454px; background: var(--navy); }
  .rule-h { position: absolute; left: 0; top: 949px; width: 794px; height: 6px; background: var(--navy); }
  .cancer { position: absolute; left: 405px; top: 636px; width: 392px; font-family: 'Oswald', sans-serif; font-weight: 500; font-size: 108px; line-height: 1; color: var(--green); text-align: center; letter-spacing: 5px; white-space: nowrap; }
  .lives { position: absolute; left: 405px; top: 746px; width: 392px; font-family: 'Oswald', sans-serif; font-weight: 600; font-size: 62px; line-height: 1; text-align: center; text-transform: uppercase; letter-spacing: -1px; white-space: nowrap; }

  .knowledge-panel { position: absolute; left: 818px; top: 57px; width: 338px; height: 615px; background: var(--navy); overflow: hidden; }
  .knowledge-panel .photo { left: 0; top: 0; width: 338px; height: 615px; background: linear-gradient(180deg, #a98a78 0%, #6a5a6a 45%, var(--navy) 72%); }
  .knowledge-text { position: absolute; right: 7px; top: 336px; text-align: right; color: var(--white); line-height: 1; }
  .knowledge-text .big { font-family: 'Oswald', sans-serif; font-size: 58px; letter-spacing: -1px; text-transform: uppercase; }
  .knowledge-text .big b { font-weight: 600; }
  .knowledge-text .big span { font-weight: 300; }
  .knowledge-text .small { font-size: 25px; font-weight: 400; margin: 10px 0 12px; letter-spacing: 0.5px; }
  .knowledge-text .note { font-size: 17px; margin-top: 16px; white-space: nowrap; }
  .knowledge-text .power { font-size: 24px; font-weight: 600; margin-top: 10px; }

  .brand { position: absolute; left: 83px; top: 972px; height: 82px; display: flex; align-items: center; gap: 14px; }
  .brand .mark { width: 80px; height: 80px; border-radius: 50%; background: var(--navy); }
  .brand .name { font-weight: 700; font-size: 25px; line-height: 1; letter-spacing: 2px; color: var(--navy); }
  .web { position: absolute; left: 820px; top: 1024px; width: 334px; text-align: right; font-size: 15px; font-weight: 600; letter-spacing: 1.6px; }
</style>
</head>
<body>
<main class="backdrop">
  <h1 class="title">
    <div class="lead">Hereditary</div>
    <div class="line">Cancer</div>
    <div class="line">Screening</div>
  </h1>
  <div class="tagline">The Test You Take For Them</div>

  <div class="photo" style="left:421px;top:62px;width:320px;height:210px" role="img" aria-label="Three generations of women smiling together outdoors"></div>
  <div class="photo soft" style="left:424px;top:290px;width:143px;height:126px" role="img" aria-label="Grandfather hugging his grandson"></div>
  <div class="photo soft" style="left:593px;top:288px;width:147px;height:124px" role="img" aria-label="Large family gathered around a table"></div>
  <div class="photo" style="left:27px;top:340px;width:347px;height:244px" role="img" aria-label="Laughing grandmother kissed by two grandchildren"></div>
  <div class="photo soft" style="left:26px;top:634px;width:348px;height:248px" role="img" aria-label="Grandparents posing with two grandchildren at home"></div>

  <div class="headline ask">Will you <strong>give</strong></div>
  <div class="headline loved">your loved ones</div>
  <div class="info-bar">the information to Beat</div>
  <div class="cancer">CANCER</div>
  <div class="lives">In their lives?</div>
  <div class="rule-v"></div>
  <div class="rule-h"></div>

  <div class="photo garden" style="left:433px;top:825px;width:136px;height:116px" role="img" aria-label="Grandfather and grandson playing in the garden"></div>
  <div class="photo garden" style="left:594px;top:825px;width:138px;height:116px" role="img" aria-label="Family relaxing together on the grass"></div>
  <div class="photo" style="left:441px;top:964px;width:286px;height:106px" role="img" aria-label="Family reading together on a sofa"></div>

  <section class="knowledge-panel">
    <div class="photo" role="img" aria-label="Grandmother embracing her granddaughter"></div>
    <div class="knowledge-text">
      <div class="big"><b>Give</b> <span>them</span></div>
      <div class="small">THE GIFT OF</div>
      <div class="big"><b>Knowledge</b></div>
      <div class="note">knowing is better than not knowing.</div>
      <div class="power">Knowledge is Power</div>
    </div>
  </section>

  <div class="photo soft" style="left:821px;top:686px;width:161px;height:147px" role="img" aria-label="Grandfather with his granddaughter"></div>
  <div class="photo soft" style="left:991px;top:686px;width:161px;height:147px" role="img" aria-label="Granddaughter hugging her grandmother"></div>
  <div class="photo garden" style="left:821px;top:843px;width:161px;height:148px" role="img" aria-label="Three generations smiling outdoors"></div>
  <div class="photo garden" style="left:991px;top:843px;width:161px;height:148px" role="img" aria-label="Grandparents with grandchildren in a park"></div>

  <div class="brand">
    <div class="mark"></div>
    <div class="name">KINFIELD<br>HEALTH<br>GROUP</div>
  </div>
  <div class="web">www.kinfieldscreening.com</div>
</main>
</body>
</html>
```